Business Card Design

I already have a company logo for my company. I have a logo for the manufacturer we represent. I want a professional business card design.

```html
<!DOCTYPE html>
<html lang="en">
<head>
<meta charset="utf-8">
<title>Signal Guard LLC — Business Card</title>
<link href="https://fonts.googleapis.com/css2?family=Open+Sans:wght@400;600;700&display=swap" rel="stylesheet">
<style>
  :root {
    --backdrop: #222222;
    --card: #1e1e22;
    --gold: #b98e2d;
    --red: #e3222b;
    --white: #f4f4f4;
  }
  * { margin: 0; padding: 0; box-sizing: border-box; }
  html, body {
    width: 1200px; height: 780px; overflow: hidden;
    background: var(--backdrop);
    font-family: "Open Sans", Arial, sans-serif;
  }
  .stage {
    position: relative; width: 1200px; height: 780px;
    display: flex; align-items: center; justify-content: center; gap: 50px;
  }
  .card {
    position: relative; width: 525px; height: 300px;
    background: var(--card); overflow: hidden;
    box-shadow: 0 18px 40px rgba(0,0,0,.45);
  }
  .card-front .swoosh { position: absolute; inset: 0; width: 100%; height: 100%; }
  .holder { position: absolute; left: 62px; top: 62px; }
  .holder-name { font-size: 25px; font-weight: 700; line-height: 1.1; }
  .holder-name .first { color: var(--gold); }
  .holder-name .last { color: var(--red); }
  .holder-title { margin-top: 6px; margin-left: 44px; font-size: 12px; color: var(--white); }
  .brand {
    position: absolute; display: flex; align-items: center; gap: 8px;
    color: var(--white); font-weight: 700; text-transform: uppercase; letter-spacing: .04em;
  }
  .card-front .brand { left: 292px; top: 70px; font-size: 19px; }
  .brand .mark { width: 14px; height: 14px; background: var(--red); flex: none; }
  .divider {
    position: absolute; left: 260px; top: 150px; width: 1.5px; height: 82px;
    background: var(--gold);
  }
  .contacts { position: absolute; left: 284px; top: 156px; list-style: none; }
  .contacts li {
    display: flex; align-items: center; gap: 9px;
    color: var(--white); font-size: 13.5px; line-height: 1.75;
  }
  .contacts svg { width: 13px; height: 13px; fill: var(--gold); flex: none; }
  .address {
    position: absolute; left: 70px; bottom: 22px;
    color: var(--white); font-size: 14px;
  }
  .card-back .texture {
    position: absolute; inset: 0;
    background: linear-gradient(135deg, #26262a 0%, #1c1c20 100%);
  }
  .card-back .brand {
    left: 50%; top: 50%; transform: translate(-50%, -50%);
    font-size: 30px; gap: 12px;
  }
  .card-back .brand .mark { width: 22px; height: 22px; }
</style>
</head>
<body>
<main class="stage">
  <section class="card card-front" aria-label="Business card front">
    <svg class="swoosh" viewBox="0 0 525 300" preserveAspectRatio="none" aria-hidden="true">
      <path d="M0 205 C120 215 300 260 525 280 L525 300 L0 300 Z" fill="var(--gold)"/>
      <path d="M14 196 C140 212 310 252 510 272" fill="none" stroke="var(--red)" stroke-width="3"/>
    </svg>
    <div class="holder">
      <h1 class="holder-name"><span class="first">Marta</span> <span class="last">Kovalenko</span></h1>
      <p class="holder-title">Managing Director</p>
    </div>
    <div class="brand"><span class="mark"></span>Signal Guard LLC</div>
    <div class="divider"></div>
    <ul class="contacts">
      <li>
        <svg viewBox="0 0 24 24"><path d="M6.6 10.8a15.1 15.1 0 0 0 6.6 6.6l2.2-2.2c.3-.3.7-.4 1-.2 1.1.4 2.3.6 3.6.6.6 0 1 .4 1 1V20c0 .6-.4 1-1 1A17 17 0 0 1 3 4c0-.6.4-1 1-1h3.5c.6 0 1 .4 1 1 0 1.3.2 2.5.6 3.6.1.3 0 .7-.2 1z"/></svg>
        (555) 214-0387
      </li>
      <li>
        <svg viewBox="0 0 24 24"><path d="M2 5h20v14H2zm2 2v.5l8 5 8-5V7l-8 5z"/></svg>
        hello@signalguardco.com
      </li>
      <li>
        <svg viewBox="0 0 24 24"><circle cx="12" cy="12" r="10"/></svg>
        www.signalguardco.com
      </li>
    </ul>
    <p class="address">1840 Meadow Ln. Suite 310 Riverton, TX 75001</p>
  </section>

  <section class="card card-back" aria-label="Business card back">
    <div class="texture" role="img" aria-label="Dark repeating brand-mark texture"></div>
    <div class="brand"><span class="mark"></span>Signal Guard LLC</div>
  </section>
</main>
</body>
</html>
```